Corvel Capital LLC

Need Professional Business cards for New Investment Fund

Target Market(s)

High Quality investors

Industry/Entity Type

Financial

Contact Information for Business Card

Phone Number +1 555 284 6190
Name Lukas Varenko
Title Fund Manager
email lv@FundCorvel.com
Website www.FundCorvel.com

Colors

Designer to choose colors to be used in the design.

Requirements
Must have
• Must have our Logo and all of the above. Must be made so lettering and loge can be raised

```html
<!DOCTYPE html>
<html lang="en">
<head>
<meta charset="utf-8">
<title>Corvel Capital LLC – Business Card</title>
<link rel="stylesheet" href="https://fonts.googleapis.com/css2?family=Jost:wght@500&family=Montserrat:wght@400&display=swap">
<style>
  :root {
    --backdrop: #c9cccb;
    --paper: #eeeeec;
    --brand-green: #2fdc2a;
    --ink: #2c2f2d;
    --ink-soft: #3a3d3b;
    --rule: #5a5d5b;
  }
  * { margin: 0; padding: 0; box-sizing: border-box; }
  html, body {
    width: 1200px; height: 800px; overflow: hidden;
    background: var(--backdrop);
  }
  .stage {
    width: 1200px; height: 800px;
    display: flex; align-items: center; justify-content: center; gap: 60px;
  }
  .card {
    width: 525px; height: 300px;
    background: var(--paper);
    position: relative;
    box-shadow: 0 2px 6px rgba(0,0,0,0.12);
    flex: none;
  }
  .card-front { display: flex; align-items: center; }
  .brand {
    width: 190px; padding-left: 40px;
    display: flex; align-items: center; gap: 10px;
  }
  .brand-square {
    width: 14px; height: 14px; background: var(--brand-green);
    flex: none;
  }
  .brand-name {
    font-family: "Jost", sans-serif; font-weight: 500;
    font-size: 21px; line-height: 1.1; color: var(--ink);
    letter-spacing: 0.4px;
  }
  .divider {
    width: 1px; height: 120px; background: var(--rule);
    margin-right: 18px; flex: none;
  }
  .details { font-family: "Montserrat", sans-serif; color: var(--ink-soft); }
  .person-name {
    font-family: "Jost", sans-serif; font-weight: 500;
    font-size: 23px; letter-spacing: 0.6px;
    color: var(--brand-green); text-transform: uppercase;
    line-height: 1.1; white-space: nowrap;
  }
  .person-title { font-size: 15px; margin-bottom: 8px; }
  .contact-list { list-style: none; }
  .contact-item {
    display: flex; align-items: center; gap: 8px;
    font-size: 15px; line-height: 1.45; white-space: nowrap;
  }
  .contact-icon { width: 12px; height: 12px; flex: none; fill: var(--brand-green); }
  .card-back .back-pattern {
    position: absolute; inset: 0;
    background: linear-gradient(135deg, #c9eec6 0%, #e3e6e3 50%, #bfe9bb 100%);
  }
</style>
</head>
<body>
<main class="stage">
  <section class="card card-front" aria-label="Business card front">
    <div class="brand">
      <span class="brand-square"></span>
      <span class="brand-name">Corvel<br>Capital</span>
    </div>
    <div class="divider"></div>
    <div class="details">
      <h1 class="person-name">Lukas Varenko</h1>
      <p class="person-title">Fund Manager</p>
      <ul class="contact-list">
        <li class="contact-item">
          <svg class="contact-icon" viewBox="0 0 12 12" aria-hidden="true"><path d="M2.4 0.8l1.8 2.2-1 1.2c0.7 1.6 2 2.9 3.6 3.6l1.2-1 2.2 1.8-1.2 2c-4.2-0.2-8.2-4.2-8.4-8.4z"/></svg>
          <span>+1 555 284 6190</span>
        </li>
        <li class="contact-item">
          <svg class="contact-icon" viewBox="0 0 12 12" aria-hidden="true"><path d="M0 2h12v8H0z M1 3l5 3.6L11 3v-0.3H1z" fill-rule="evenodd"/></svg>
          <span>lv@FundCorvel.com</span>
        </li>
        <li class="contact-item">
          <svg class="contact-icon" viewBox="0 0 12 12" aria-hidden="true"><circle cx="6" cy="6" r="6"/><path d="M1 6h10M6 1c-2.4 2.8-2.4 7.2 0 10M6 1c2.4 2.8 2.4 7.2 0 10" stroke="#eeeeec" stroke-width="0.9" fill="none"/></svg>
          <span>www.FundCorvel.com</span>
        </li>
      </ul>
    </div>
  </section>
  <section class="card card-back" aria-label="Business card back">
    <div class="back-pattern" role="img" aria-label="Repeating pattern of the brand symbol in green and charcoal"></div>
  </section>
</main>
</body>
</html>
```